Social Media App Needs PPT Template

We need a PowerPoint template for a new social media company based in the DC area called "Bold Ledger." We provide an interactive digital platform for executives to share actionable advice. We would like to see designs that use our orange logo color as an accent, but are mainly grey, white, and black. The final design should communicate clean, chic, modern, and professional.

Target Market(s)

Executives

Industry/Entity Type

Information Technology

Font styles to use
Sans Serif

Colors
f78f20
fbe7d2
ffffff
000000
e8e8e8
757575

Requirements
Must have
• My project must have title page and many options for the body of the ppt (graphs, tables, etc). It also needs to be easy to modify. I must have someone who is experienced in creating powerpoint templates.
Nice to have
• It would be nice to have a very modern and clean design that includes the logo on every page, but still leaves a lot of room for the content of the slide
Should not have
• My design project should not look to busy.

```html
<!DOCTYPE html>
<html lang="en">
<head>
<meta charset="utf-8">
<title>Bold Ledger – About Our Company</title>
<link href="https://fonts.googleapis.com/css2?family=Lato:wght@300;400;700&display=swap" rel="stylesheet">
<style>
  :root {
    --board: #929292;
    --orange: #f0901e;
    --orange-deep: #e5801a;
    --charcoal: #454545;
    --grey-area: #a2a3a6;
    --ink: #4a4a4a;
    --white: #ffffff;
  }
  html, body {
    margin: 0; padding: 0;
    width: 1200px; height: 960px;
    overflow: hidden;
    background: var(--board);
    font-family: "Lato", sans-serif;
  }
  .page-label {
    position: absolute; top: 44px; left: 0; width: 1200px;
    text-align: center; color: var(--white);
    font-weight: 300; font-size: 25px; margin: 0;
  }
  .slide {
    position: absolute; left: 87px; top: 128px;
    width: 1046px; height: 784px;
    background: radial-gradient(ellipse at 55% 30%, #ffffff 0%, #f4f4f4 55%, #ececec 100%);
    overflow: hidden;
  }
  .slide-art { position: absolute; inset: 0; width: 1046px; height: 784px; }
  .slide-title {
    position: absolute; left: 32px; top: 70px; margin: 0;
    color: var(--white); font-weight: 300; font-size: 39px; letter-spacing: 0.2px;
  }
  .brand {
    position: absolute; left: 850px; top: 72px;
    display: flex; align-items: center; gap: 10px;
    color: var(--white); font-weight: 700; font-size: 24px;
  }
  .brand-dot { width: 26px; height: 26px; border-radius: 50%; background: var(--orange); }
  .axis-label {
    position: absolute; width: 30px; text-align: right;
    color: var(--ink); font-size: 16px; line-height: 16px;
  }
  .category {
    position: absolute; top: 488px; color: var(--ink); font-size: 17px;
  }
  .legend { position: absolute; left: 921px; top: 228px; margin: 0; padding: 0; list-style: none; }
  .legend li {
    display: flex; align-items: center; gap: 6px;
    color: var(--ink); font-size: 18px; height: 26px;
  }
  .legend i { width: 10px; height: 10px; display: inline-block; }
  .body-copy {
    position: absolute; left: 53px; top: 547px; width: 946px; margin: 0;
    color: var(--ink); font-size: 18px; line-height: 26.4px; text-align: justify;
  }
  .footer-text {
    position: absolute; left: 28px; top: 748px;
    color: #e6e6e6; font-size: 14px; margin: 0;
  }
</style>
</head>
<body>
  <p class="page-label">Page 7</p>

  <section class="slide">
    <svg class="slide-art" viewBox="109 160 1307 980" aria-hidden="true">
      <!-- header -->
      <polygon points="1125,203 1416,203 1416,215 1114,215" fill="var(--orange)"/>
      <polygon points="109,221 1100,221 990,323 109,323" fill="var(--orange-deep)"/>
      <polygon points="109,221 900,221 815,303 109,303" fill="#eb8a1f" opacity="0.6"/>
      <polygon points="1110,221 1416,221 1416,323 1000,323" fill="var(--charcoal)"/>
      <polygon points="109,330 990,330 978,342 109,342" fill="var(--charcoal)"/>

      <!-- chart grid -->
      <g stroke="#9a9a9a" stroke-width="1" stroke-dasharray="8 6">
        <line x1="215" y1="452" x2="1222" y2="452"/>
        <line x1="215" y1="513" x2="1222" y2="513"/>
        <line x1="215" y1="571" x2="1222" y2="571"/>
        <line x1="215" y1="632" x2="1222" y2="632"/>
        <line x1="215" y1="690" x2="1222" y2="690"/>
      </g>

      <!-- series areas -->
      <polygon points="585,543 615,532 1220,475 1220,748 585,748" fill="var(--charcoal)"/>
      <polygon points="215,648 445,528 930,570 1100,590 1220,600 1220,748 215,748" fill="var(--orange)"/>
      <polygon points="215,648 445,605 605,580 930,622 1100,590 1220,570 1220,748 215,748" fill="var(--grey-area)"/>

      <!-- axis -->
      <line x1="215" y1="452" x2="215" y2="749" stroke="#8a8a8a" stroke-width="1"/>
      <line x1="209" y1="748" x2="215" y2="748" stroke="#8a8a8a" stroke-width="1"/>

      <!-- footer -->
      <polygon points="109,1088 482,1088 443,1126 109,1126" fill="var(--charcoal)"/>
      <polygon points="490,1088 1416,1088 1416,1126 452,1126" fill="var(--orange-deep)"/>
    </svg>

    <h1 class="slide-title">About Our Company</h1>
    <div class="brand"><span class="brand-dot"></span>Bold Ledger</div>

    <span class="axis-label" style="left:28px; top:229px">5</span>
    <span class="axis-label" style="left:28px; top:278px">4</span>
    <span class="axis-label" style="left:28px; top:323px">3</span>
    <span class="axis-label" style="left:28px; top:371px">2</span>
    <span class="axis-label" style="left:28px; top:418px">1</span>
    <span class="axis-label" style="left:28px; top:466px">0</span>

    <span class="category" style="left:85px">Category 1</span>
    <span class="category" style="left:427px">Category 2</span>
    <span class="category" style="left:786px">Category 3</span>

    <ul class="legend">
      <li><i style="background:var(--grey-area)"></i>Series 1</li>
      <li><i style="background:var(--orange)"></i>Series 2</li>
      <li><i style="background:var(--charcoal)"></i>Series 3</li>
    </ul>

    <p class="body-copy">Duis autem vel eum iriure dolor in hendrerit in vulputate velit esse molestie consequat, vel illum dolore eu feugiat nulla facilisis at vero eros et accumsan et iusto odio dignissim qui blandit praesent luptatum zzril delenit augue duis dolore te feugait nulla facilisi. Nam liber tempor cum soluta nobis eleifend option congue nihil imperdiet doming id quod mazim placerat facer possim assum.</p>

    <p class="footer-text">www.boldledger.com &nbsp;|&nbsp; Page 5</p>
  </section>
</body>
</html>
```